Yoga class opening. Little schedule for JUNE JULY and AUGUST

Flyer to promote an opening yoga class. The color of the docx haven't to be respected.

We want something joyfull, professional, clean and serious.

About the logo we oppened a contest at the same time so at the moment there is no logo but the logo color will be simple.

The phone number will change so you can poste a random one for the design that i can change by myself.

i recieved many creation in both side BUT i want something in 1 side :)

Target Market(s)

Yoga student. all age

Industry/Entity Type

It Professional

Logo Text

Yoga fern

Font styles to use
Sans Serif

Requirements
Must have
• The text present on the docx
Nice to have
• Some symbols about yoga ( Namasté signs, mandala, ... )
Should not have
• Not too much details it has to be clear.

```html
<!DOCTYPE html>
<html lang="fr">
<head>
<meta charset="utf-8">
<title>Yoga Fern – Flyer d'ouverture</title>
<link href="https://fonts.googleapis.com/css2?family=Bebas+Neue&family=Raleway:wght@400;500&family=Dancing+Script:wght@500&display=swap" rel="stylesheet">
<style>
  :root{
    --green:#4aa63a;
    --green-dark:#2f8a2c;
    --green-light:#8cc63f;
    --green-pale:#c9e3a0;
    --lime:#a4cf3b;
    --text-grey:#8a8a8a;
    --paper:#ffffff;
    --backdrop:#eeeeee;
    --white:#ffffff;
  }
  *{margin:0;padding:0;box-sizing:border-box}
  html,body{width:1041px;height:1200px;overflow:hidden;background:var(--backdrop)}
  .flyer-wrap{position:absolute;left:110px;top:18px;width:820px;height:1164px}
  .flyer{position:absolute;left:0;top:0;width:620px;height:880px;background:var(--paper);
    transform:scale(1.3226);transform-origin:0 0;overflow:hidden;
    font-family:'Raleway',sans-serif;box-shadow:0 2px 10px rgba(0,0,0,.12)}
  .flyer-art{position:absolute;inset:0;width:620px;height:880px}
  .heading{font-family:'Bebas Neue',sans-serif;font-weight:400;letter-spacing:.3px;position:absolute;white-space:nowrap;line-height:1}
  .brand{position:absolute;left:22px;top:50px;width:150px;text-align:center}
  .brand-mark{width:58px;height:58px;border-radius:50%;background:var(--green-light);margin:0 auto 8px}
  .brand-name{font-family:'Raleway',sans-serif;font-weight:500;font-size:26px;color:var(--green-dark)}
  .intro-new{left:347px;top:92px;font-size:36px;color:var(--white)}
  .bar{position:absolute;background:var(--green);color:var(--white);font-family:'Bebas Neue',sans-serif;
    white-space:nowrap;line-height:1;display:flex;align-items:center;padding-left:8px}
  .studio-bar{left:336px;top:152px;width:266px;height:30px;font-size:21px}
  .opening{left:343px;top:189px;font-size:20.5px;color:var(--white);line-height:1.08}
  .opening-note{position:absolute;left:343px;top:260px;width:260px;font-size:8.6px;color:var(--white);line-height:1.25}
  .month{font-size:26px;color:var(--green-light);left:27px}
  .course-bar{left:20px;height:24px;font-size:15.5px}
  .dates{position:absolute;left:30px;font-size:8.3px;color:var(--text-grey);line-height:1.3;white-space:nowrap}
  .badge-text{position:absolute;left:393px;top:608px;width:210px;transform:rotate(-8deg);text-align:center}
  .badge-title{font-family:'Bebas Neue',sans-serif;font-size:25px;color:var(--white);line-height:.98}
  .badge-date{display:inline-block;margin-top:6px;background:var(--green);color:var(--white);
    font-family:'Bebas Neue',sans-serif;font-size:29px;padding:3px 10px 1px}
  .contact-bar{left:460px;top:783px;width:152px;height:20px;font-size:14px}
  .contact{position:absolute;left:465px;display:flex;align-items:center;gap:7px;font-family:'Bebas Neue',sans-serif;
    font-size:14px;color:var(--white)}
  .contact-dot{width:17px;height:17px;border-radius:50%;background:var(--white);display:flex;align-items:center;justify-content:center}
  .greeting{position:absolute;left:292px;top:841px;font-family:'Dancing Script',cursive;font-size:20px;color:var(--white)}
</style>
</head>
<body>
<div class="flyer-wrap">
<main class="flyer">
  <svg class="flyer-art" viewBox="0 0 620 880" aria-hidden="false">
    <defs>
      <linearGradient id="photoTone" x1="0" y1="0" x2="1" y2="1">
        <stop offset="0" stop-color="#9fcf5a"/>
        <stop offset=".55" stop-color="#bcd98a"/>
        <stop offset="1" stop-color="#7fb24a"/>
      </linearGradient>
      <linearGradient id="footTone" x1="0" y1="0" x2="1" y2="0">
        <stop offset="0" stop-color="#6dbb3c"/>
        <stop offset="1" stop-color="#a6d14a"/>
      </linearGradient>
      <radialGradient id="badgeTone" cx=".5" cy=".5" r=".5">
        <stop offset="0" stop-color="#a9d64c"/>
        <stop offset="1" stop-color="#7dbf3a"/>
      </radialGradient>
    </defs>
    <!-- photo area -->
    <path role="img" aria-label="Photo: woman in tree pose above a misty valley at sunrise"
          d="M190 265 C320 220 420 90 475 0 L620 0 L620 610 Z" fill="url(#photoTone)"/>
    <!-- top swoosh band -->
    <path d="M0 255 C120 300 300 190 470 0 L505 0 C330 220 140 320 0 285 Z" fill="var(--green)"/>
    <path d="M0 238 C110 275 280 180 440 0 L452 0 C290 195 120 290 0 250 Z" fill="var(--green-light)"/>
    <path d="M0 288 C150 330 350 210 520 0 L526 0 C360 220 150 345 0 300 Z" fill="var(--green-pale)"/>
    <!-- diagonal ribbon -->
    <path d="M150 250 C330 220 470 420 620 560 L620 610 C470 470 330 260 150 265 Z" fill="#d7ebb8" opacity=".85"/>
    <!-- announcement badge -->
    <circle cx="490" cy="672" r="118" fill="#b9dd7a"/>
    <circle cx="490" cy="672" r="104" fill="url(#badgeTone)"/>
    <!-- footer wave -->
    <path d="M0 842 C200 880 430 750 620 715 L620 880 L0 880 Z" fill="#e8f2d8"/>
    <path d="M0 852 C210 888 440 762 620 728 L620 880 L0 880 Z" fill="url(#footTone)"/>
  </svg>

  <header class="brand">
    <div class="brand-mark"></div>
    <div class="brand-name">Yoga Fern</div>
  </header>

  <section class="intro">
    <h1 class="heading intro-new">NEW !!</h1>
    <div class="bar studio-bar">YOUR YOGA STUDIO IN IXELLES</div>
    <p class="heading opening">THE OPENING IN 6 JUIN 2016<br>212 RUE DES TILLEULS<br>1050 IXELLES</p>
    <p class="opening-note">En attendant le planning des cours de la rentrée, YOGA FERN vous propose ses stages et ateliers d'été.</p>
  </section>

  <section class="schedule">
    <h2 class="heading month" style="top:300px">JUIN</h2>
    <div class="bar course-bar" style="top:330px;width:240px">STAGE DÉCOUVERTE DU YOGA 10H00 85 €</div>
    <p class="dates" style="top:359px">Du lundi 6 au vendredi 10 juin : 10h00 à 12h00 ou 18h00 à 20h00<br>Du lundi 13 au vendredi 17 juin : 10h00 à 12h00 ou 18h00 à 20h00<br>Du lundi 20 au vendredi 24 juin : 10h00 à 12h00 ou 18h00 à 20h00<br>Du lundi 27 au vendredi 1er juillet : 10h00 à 12h00 ou 18h00 à 20h00</p>
    <div class="bar course-bar" style="top:408px;width:344px">ATELIER GESTION DU STRESS YOGA/SOPHROLOGIE 2H00 28 €</div>
    <p class="dates" style="top:437px">Samedi 11 juin 10h30 à 12h30<br>Samedi 11 juin 15h à 17h00<br>Dimanche 12 juin 10h30 à 12h30<br>Dimanche 12 juin 14h à 16h00</p>

    <h2 class="heading month" style="top:500px">JUILLET</h2>
    <div class="bar course-bar" style="top:528px;width:240px">STAGE INITIATION À L'ASHTANGA 10H00 85 €</div>
    <p class="dates" style="top:558px">Du lundi 4 au vendredi 8 juillet : 10h00 à 12h00 ou 18h00 à 20h00<br>Du lundi 11 au vendredi 15 juillet : 10h00 à 12h00 ou 18h00 à 20h00<br>Du lundi 18 au vendredi 22 juillet : 10h00 à 12h00 ou 18h00 à 20h00<br>Du lundi 25 au vendredi 29 juillet : 10h00 à 12h00 ou 18h00 à 20h00</p>
    <div class="bar course-bar" style="top:608px;width:344px">ATELIER GESTION DU STRESS YOGA/SOPHROLOGIE 2H00 28 €</div>
    <p class="dates" style="top:639px">Samedi 9 juillet 10h30 à 12h30<br>Samedi 9 juillet 15h00 à 17h00<br>Dimanche 10 juillet 10h30 à 12h30<br>Dimanche 10 juillet 14h00 à 16h00</p>

    <h2 class="heading month" style="top:700px">AOUT</h2>
    <div class="bar course-bar" style="top:729px;width:240px">STAGE DÉCOUVERTE DU YOGA 10H00 85 €</div>
    <p class="dates" style="top:759px">Du lundi 1er au vendredi 5 août : 10h00 à 12h00 ou 18h00 à 20h00<br>Du lundi 8 au vendredi 12 août : 10h00 à 12h00 ou 18h00 à 20h00<br>Du lundi 15 au vendredi 19 août : 10h00 à 12h00 ou 18h00 à 20h00<br>Du lundi 22 au vendredi 26 août : 10h00 à 12h00 ou 18h00 à 20h00</p>
  </section>

  <section class="badge-text">
    <p class="badge-title">DÉMARRAGE DU<br>PLANNING ANNUEL LE</p>
    <p class="badge-date">5 SEPTEMBRE 2016</p>
  </section>

  <footer>
    <div class="bar contact-bar">PLUS D'INFO ET INSCRIPTION</div>
    <p class="contact" style="top:813px"><span class="contact-dot"></span>YOGA FERN</p>
    <p class="contact" style="top:841px"><span class="contact-dot">
      <svg width="11" height="11" viewBox="0 0 24 24"><path d="M6.6 10.8a15 15 0 0 0 6.6 6.6l2.2-2.2a1 1 0 0 1 1-.25 11.4 11.4 0 0 0 3.6.57 1 1 0 0 1 1 1V20a1 1 0 0 1-1 1A17 17 0 0 1 3 4a1 1 0 0 1 1-1h3.5a1 1 0 0 1 1 1c0 1.25.2 2.45.57 3.57a1 1 0 0 1-.25 1z" fill="var(--green-light)"/></svg>
    </span>010 2468 135</p>
    <p class="greeting">Un belete a tous!</p>
  </footer>
</main>
</div>
</body>
</html>
```